Looking for a cool & simple business-card-design for digital agency

Hi!

We are a web agency that offers Reputation Management, Vextor & Seo Services and software development. We like cool things, we like innovative styles.

We have uploaded our logo.

Project Deadline Extended Reason: Client does not want any designs with the colorful logo. Please send us submissions ONLY with the blac and white logo. What the client would like to see:1) Back of the card: is a silver logo on a black background2) front of the card with all the data, please use white background and black logo thank you Added Friday, May 8, 2015

Industry/Entity Type

Software

```html
<!DOCTYPE html>
<html lang="de">
<head>
<meta charset="utf-8">
<title>Kaldera – Visitenkarte</title>
<link href="https://fonts.googleapis.com/css2?family=Questrial&display=swap" rel="stylesheet">
<style>
  :root {
    --backdrop: #3b322d;
    --card-black: #121212;
    --card-white: #f4f4f2;
    --silver: #c9c9c9;
    --ink: #1e1e1e;
    --ink-soft: #3a3a3a;
  }
  * { margin: 0; padding: 0; box-sizing: border-box; }
  html, body {
    width: 1200px;
    height: 819px;
    overflow: hidden;
    background: var(--backdrop);
    font-family: "Questrial", "Century Gothic", sans-serif;
  }
  .stage {
    position: relative;
    width: 1200px;
    height: 819px;
  }
  .card {
    position: absolute;
    top: 235px;
    width: 540px;
    height: 349px;
    box-shadow: 0 18px 40px rgba(0,0,0,0.45);
  }
  .card--back {
    left: 40px;
    background: var(--card-black);
    display: flex;
    align-items: center;
    justify-content: center;
  }
  .card--front {
    left: 620px;
    background: var(--card-white);
  }
  .brand {
    display: flex;
    flex-direction: column;
    align-items: flex-start;
  }
  .brand__row {
    display: flex;
    align-items: center;
    gap: 12px;
  }
  .brand__mark {
    width: 26px;
    height: 26px;
  }
  .brand__name {
    font-size: 44px;
    line-height: 1;
    letter-spacing: 1px;
  }
  .brand__tagline {
    margin-top: 6px;
    margin-left: 38px;
    font-size: 13px;
    letter-spacing: 4.2px;
  }
  .card--back .brand__mark { background: var(--silver); }
  .card--back .brand__name,
  .card--back .brand__tagline { color: var(--silver); }

  .card--front .brand {
    position: absolute;
    top: 48px;
    right: 40px;
  }
  .card--front .brand__mark { width: 20px; height: 20px; background: var(--ink); }
  .card--front .brand__name { font-size: 34px; color: var(--ink); }
  .card--front .brand__tagline { font-size: 10px; letter-spacing: 3.4px; margin-left: 32px; color: var(--ink); }

  .contact {
    position: absolute;
    left: 40px;
    bottom: 48px;
    color: var(--ink-soft);
    font-size: 12.5px;
    line-height: 1.55;
  }
  .contact__name {
    font-size: 16px;
    font-weight: 700;
    letter-spacing: 0.5px;
    color: var(--ink);
  }
  .contact__role {
    font-size: 13px;
    margin-bottom: 8px;
  }
  .contact__label {
    font-weight: 700;
    color: var(--ink);
  }
</style>
</head>
<body>
<main class="stage">
  <section class="card card--back" aria-label="Kartenrückseite">
    <div class="brand">
      <div class="brand__row">
        <span class="brand__mark"></span>
        <span class="brand__name">Kaldera</span>
      </div>
      <span class="brand__tagline">DIGITALE STRATEGIEN</span>
    </div>
  </section>

  <section class="card card--front" aria-label="Kartenvorderseite">
    <div class="brand">
      <div class="brand__row">
        <span class="brand__mark"></span>
        <span class="brand__name">Kaldera</span>
      </div>
      <span class="brand__tagline">DIGITALE STRATEGIEN</span>
    </div>

    <div class="contact">
      <p class="contact__name">JONAS WEBER</p>
      <p class="contact__role">Managing Director</p>
      <p>Brunnenstraße 48, 20095 Hamburg, Germany</p>
      <p><span class="contact__label">Tel:</span> +49-(40)-55512-1020 · <span class="contact__label">Fax:</span> +49-(40)-55512-1030</p>
      <p><span class="contact__label">Email:</span> jonas@kalderadigital.de · <span class="contact__label">Web:</span> www.kalderadigital.de</p>
    </div>
  </section>
</main>
</body>
</html>
```